Marlowby Services Website Design

We have most content but require a professional design. We have a logo already and will need it utilized along with several of the photos from the attached documentation.
First page should have our mission and Vision and the synapsis provided in the word document. Visitors will be prompted to select from one of our 3 divisions from this page.
Each division will have the same list of tabs : About, Services, Safety, Careers and Contact.
Photos on each divisions page should be representative of the divisions offerings. The word doc attached contains the requested content and we are open to edits that would complement and fill the website.
I like the Quorvane site www.quorvane.example - they are our competition so cant be modeled directly after this.
Please include prompts to request quote at each service page. align the format of the geotechnical page to the other 2 divisions.
I used chat gpt for some of the content so will need it optimized for SCO.

```html
<!DOCTYPE html>
<html lang="en">
<head>
<meta charset="utf-8">
<title>Marlowby Services</title>
<link href="https://fonts.googleapis.com/css2?family=Roboto:wght@400;500;700;900&display=swap" rel="stylesheet">
<style>
:root{
  --red:#ed1c24;
  --ink:#222;
  --text:#666;
  --black:#000;
  --white:#fff;
  --footer:#141414;
}
*{margin:0;padding:0;box-sizing:border-box}
html,body{width:1200px;height:2790px;overflow:hidden;background:var(--white);font-family:"Roboto",Arial,sans-serif;color:var(--ink)}
.page{position:relative;width:1200px;height:2790px}
.abs{position:absolute}
.site-header{left:0;top:0;width:1200px;height:75px;background:var(--white)}
.logo{left:110px;top:20px;font-size:27px;font-weight:900;color:var(--red);letter-spacing:2px}
.nav{left:465px;top:25px;display:flex;gap:32px;font-size:15px;color:#333}
.nav .active{color:var(--red)}
.quote-btn{left:939px;top:14px;width:148px;height:40px;border-radius:20px;background:var(--red);color:var(--white);font-size:14px;font-weight:700;display:flex;align-items:center;justify-content:center}
.header-rule{left:0;top:75px;width:1200px;height:5px;background:var(--red)}
.nav-marker{left:474px;top:64px}
.hero{left:0;top:80px;width:1200px;height:595px;background:linear-gradient(160deg,#a38a68 0%,#8e7656 40%,#7b654a 70%,#5c4b38 100%)}
.hero-truck{left:680px;top:130px;width:270px;height:400px;background:linear-gradient(180deg,#e8e8e8,#c9c9c9);border-radius:6px;opacity:.85}
.vision-card{left:112px;top:232px;width:430px;height:286px;background:var(--white)}
.vision-frame{left:17px;top:18px;width:395px;height:250px;border:2px solid var(--red)}
.vision-card h1{position:absolute;left:48px;top:44px;font-size:38px;font-weight:700;color:var(--ink)}
.vision-card h2{position:absolute;left:50px;top:98px;font-size:21px;font-weight:700;color:var(--red)}
.vision-card p{position:absolute;left:49px;top:140px;width:350px;font-size:13.5px;line-height:21.5px;color:#333}
.dots{left:567px;top:592px;display:flex;gap:10px}
.dots span{width:9px;height:9px;border-radius:50%;background:var(--white)}
.dots .on{background:var(--red)}
.section-title{left:0;width:1200px;text-align:center;font-size:44px;font-weight:700;color:var(--ink)}
.title-rule{left:565px;width:70px;height:2px;background:var(--red)}
.mission-text{left:229px;top:848px;width:742px;font-size:14px;line-height:21.5px;color:var(--text);text-align:justify;text-align-last:center}
.service-card{width:356px;height:239px;color:var(--white);display:flex;flex-direction:column;align-items:center}
.service-card.dark{background:var(--black)}
.service-card.red{background:var(--red)}
.service-card svg{margin-top:38px;width:80px;height:80px}
.service-card h3{margin-top:14px;font-size:17px;font-weight:700}
.service-card .mini-rule{margin-top:16px;width:26px;height:2px;background:var(--red)}
.service-card.red .mini-rule{background:var(--white)}
.division-photo{top:1863px;width:306px;height:343px}
.division-label{top:2233px;width:306px;text-align:center;font-size:21px;font-weight:500;color:#333;line-height:30px}
.site-footer{left:0;top:2393px;width:1200px;height:397px;background:radial-gradient(ellipse at 55% 35%,#2b2b2b 0%,#1a1a1a 45%,var(--footer) 100%);color:var(--white)}
.footer-col h4{font-size:20px;font-weight:700}
.quick-links{left:182px;top:85px}
.quick-links ul{list-style:none;margin-top:18px;font-size:14px;line-height:25.7px}
.contact-col{left:397px;top:85px}
.contact-item{display:flex;gap:13px;font-size:14px;line-height:25.5px;margin-top:16px}
.contact-item .ico{width:30px;height:30px;border-radius:50%;background:var(--red);flex:none;display:flex;align-items:center;justify-content:center}
.newsletter{left:697px;top:85px}
.email-field{position:absolute;left:-3px;top:47px;width:328px;height:43px;border:1px solid #777;border-radius:22px;font-size:14px;padding:12px 0 0 25px}
.subscribe-btn{position:absolute;left:-3px;top:100px;width:148px;height:43px;border-radius:22px;background:var(--red);font-size:13px;display:flex;align-items:center;justify-content:center}
.copyright{left:0;top:333px;width:1200px;text-align:center;font-size:15px}
</style>
</head>
<body>
<div class="page">
  <header class="site-header abs">
    <div class="logo abs">MARLOWBY</div>
    <nav class="nav abs"><span class="active">Home</span><span>About</span><span>Services</span><span>Safety</span><span>Careers</span><span>Contact</span></nav>
    <div class="quote-btn abs">GET A QUOTE</div>
  </header>
  <div class="header-rule abs"></div>
  <svg class="nav-marker abs" width="12" height="12"><path d="M6 0 L12 12 L0 12 Z" fill="#ed1c24"/></svg>

  <section class="hero abs" role="img" aria-label="Aerial photo of a white boom truck parked on a dirt lot beside a field">
    <div class="hero-truck abs"></div>
  </section>
  <div class="vision-card abs">
    <div class="vision-frame abs"></div>
    <h1>MARLOWBY</h1>
    <h2>Our Vision</h2>
    <p>To be the leading provider of aerial access, geotechnical drilling, and service solutions, setting the standard for excellence in safety, efficiency, and environmental stewardship.</p>
  </div>
  <div class="dots abs"><span></span><span class="on"></span><span></span><span></span></div>

  <h2 class="section-title abs" style="top:762px">MISSION STATEMENT</h2>
  <div class="title-rule abs" style="top:831px"></div>
  <p class="mission-text abs">At Marlowby, our mission is to deliver unparalleled aerial access, geotechnical drilling, and service and maintenance solutions, consistently exceeding our clients' expectations. We strive to achieve this by investing in cutting-edge technology, fostering a culture of safety and continuous improvement, and prioritizing environmental sustainability. Through collaboration, integrity, and dedication, we aim to contribute to the success of our clients while maintaining the highest standards of quality and professionalism.</p>

  <h2 class="section-title abs" style="top:1044px">MARLOWBY SERVICES</h2>
  <div class="title-rule abs" style="top:1113px"></div>

  <div class="service-card dark abs" style="left:22px;top:1149px">
    <svg viewBox="0 0 80 80" fill="none" stroke="#fff" stroke-width="3"><path d="M52 6 L72 13 V30 C72 42 62 50 52 54 C42 50 32 42 32 30 V13 Z"/><path d="M43 30 L50 37 L62 24"/><path d="M6 48 H40 V76 H10 Z M6 48 L14 40 H34 L40 48 M22 48 V76"/></svg>
    <h3>Delivering safe</h3><div class="mini-rule"></div>
  </div>
  <div class="service-card red abs" style="left:422px;top:1149px">
    <svg viewBox="0 0 80 80" fill="none" stroke="#fff" stroke-width="3"><circle cx="40" cy="16" r="11"/><path d="M35 16 L39 20 L46 12"/><path d="M6 40 L20 28 L34 40 L26 48 Z M74 40 L60 28 L46 40 L54 48 Z M26 48 L40 66 L54 48 M32 56 L38 50 M38 62 L44 56"/></svg>
    <h3>Reliable Aerial Access</h3><div class="mini-rule"></div>
  </div>
  <div class="service-card dark abs" style="left:822px;top:1149px">
    <svg viewBox="0 0 80 80" fill="none" stroke="#fff" stroke-width="3"><path d="M6 76 H74"/><path d="M12 76 V40 H30 V76 M34 76 V14 H54 V76 M58 76 V48 H70 V76"/><path d="M40 24 H48 M40 34 H48 M40 44 H48 M16 50 H26 M16 60 H26"/><circle cx="21" cy="32" r="5"/></svg>
    <h3>Maintenance Services to Oil&amp;Gas</h3><div class="mini-rule"></div>
  </div>
  <div class="service-card red abs" style="left:22px;top:1432px">
    <svg viewBox="0 0 80 80" fill="none" stroke="#fff" stroke-width="3"><path d="M24 30 A16 16 0 0 1 56 30 Z M20 30 H60"/><path d="M27 34 C27 46 53 46 53 34"/><path d="M14 76 V62 C14 54 24 50 30 50 L40 60 L50 50 C56 50 66 54 66 62 V76 Z"/><circle cx="16" cy="18" r="8"/></svg>
    <h3>Construction</h3><div class="mini-rule"></div>
  </div>
  <div class="service-card dark abs" style="left:422px;top:1432px">
    <svg viewBox="0 0 80 80" fill="none" stroke="#fff" stroke-width="3"><circle cx="40" cy="40" r="24"/><circle cx="40" cy="40" r="14"/><circle cx="40" cy="35" r="5"/><path d="M31 48 C33 42 47 42 49 48"/><path d="M40 6 V14 M40 66 V74 M6 40 H14 M66 40 H74 M16 16 L22 22 M58 58 L64 64 M64 16 L58 22 M16 64 L22 58"/></svg>
    <h3>Utility</h3><div class="mini-rule"></div>
  </div>
  <div class="service-card red abs" style="left:822px;top:1432px">
    <svg viewBox="0 0 80 80" fill="none" stroke="#fff" stroke-width="3"><path d="M30 6 V40 M24 14 H36 M24 26 H36"/><path d="M8 46 H72 L66 56 H14 Z M18 56 V76 M40 56 V76 M62 56 V76 M12 76 H68"/><path d="M46 46 V32 L58 26 V46 M62 30 L72 18"/></svg>
    <h3>Renewable Energy Industries</h3><div class="mini-rule"></div>
  </div>

  <h2 class="section-title abs" style="top:1764px">SELECT DIVISION</h2>
  <div class="title-rule abs" style="top:1833px"></div>

  <div class="division-photo abs" style="left:110px;background:linear-gradient(170deg,#b7bcb4,#8f8f7d 55%,#6a6b5c)" role="img" aria-label="Aerial access lift beside a roadside sign over a small town"></div>
  <div class="division-photo abs" style="left:446px;background:linear-gradient(160deg,#a9ada4,#8b8d84 50%,#5f6a52)" role="img" aria-label="Top-down view of a drilling rig with extended boom on a paved lot"></div>
  <div class="division-photo abs" style="left:781px;background:linear-gradient(180deg,#2f4f66,#4a4a4c 35%,#7c6a52 70%,#3f3a35)" role="img" aria-label="Aerial night view of an energy facility with storage tanks"></div>
  <div class="division-label abs" style="left:104px">AERIAL ACCESS</div>
  <div class="division-label abs" style="left:440px">GEOTECHNICAL DRILLING</div>
  <div class="division-label abs" style="left:775px">RENEWABLE ENERGY<br>SERVICES</div>

  <footer class="site-footer abs" role="img" aria-label="Darkened aerial town photo behind the footer">
    <div class="footer-col quick-links abs">
      <h4>Qucik Links</h4>
      <ul><li>Home</li><li>About</li><li>Services</li><li>Safety</li><li>Careers</li><li>Contact</li></ul>
    </div>
    <div class="footer-col contact-col abs">
      <h4>Contact Us</h4>
      <div class="contact-item"><span class="ico"><svg width="12" height="14" viewBox="0 0 12 14"><path d="M6 0 C2.7 0 0 2.5 0 5.6 C0 9.5 6 14 6 14 C6 14 12 9.5 12 5.6 C12 2.5 9.3 0 6 0 Z" fill="#fff"/><circle cx="6" cy="5.5" r="2" fill="#ed1c24"/></svg></span><span>Lorem ipsum dolor<br>sit amet</span></div>
      <div class="contact-item" style="margin-top:20px"><span class="ico"><svg width="13" height="13" viewBox="0 0 24 24"><path d="M6.6 10.8 C8 13.6 10.4 16 13.2 17.4 L15.4 15.2 C15.7 14.9 16.1 14.8 16.4 15 C17.5 15.4 18.7 15.6 20 15.6 C20.6 15.6 21 16 21 16.6 V20 C21 20.6 20.6 21 20 21 C10.6 21 3 13.4 3 4 C3 3.4 3.4 3 4 3 H7.5 C8.1 3 8.5 3.4 8.5 4 C8.5 5.3 8.7 6.5 9.1 7.6 C9.2 7.9 9.1 8.3 8.9 8.6 Z" fill="#fff"/></svg></span><span>+1 555 010 0188</span></div>
      <div class="contact-item" style="margin-top:20px"><span class="ico"><svg width="14" height="10" viewBox="0 0 14 10"><rect width="14" height="10" rx="1" fill="#fff"/><path d="M0 1 L7 6 L14 1" stroke="#ed1c24" stroke-width="1.4" fill="none"/></svg></span><span>info@marlowby.example</span></div>
    </div>
    <div class="footer-col newsletter abs">
      <h4>Subscribe to Our Newsletter</h4>
      <div class="email-field">Email address</div>
      <div class="subscribe-btn">SUBSCRIBE</div>
    </div>
    <div class="copyright abs">© Copyrights 2024 Marlowby Services | All Rights Reserved | Privacy Policy</div>
  </footer>
</div>
</body>
</html>
```